Structural Engineering Business Card

Brookvane Drafting does residential house plans for clients in Central Florida. Would like simple but elegant business card that is appropriate for a house plan engineering company. Prefer black business card with black/white them but open to other shades of blue. I uploaded a sample card that I came across that looked good but please come up with your own creative designs.

Contact Information for Business Card

Name, Title, Phone, Email, Address, website

```html
<!DOCTYPE html>
<html lang="en">
<head>
<meta charset="utf-8">
<title>Brookvane Drafting — Business Card</title>
<link rel="stylesheet" href="https://fonts.googleapis.com/css2?family=Open+Sans:wght@400;700;800&display=swap">
<style>
  :root {
    --backdrop: #8a8a8a;
    --card-white: #ffffff;
    --card-black: #1b1b1b;
    --ink: #111111;
    --ink-soft: #3a3a3a;
    --gloss: #2c2c2c;
  }
  * { box-sizing: border-box; margin: 0; padding: 0; }
  html, body { width: 1200px; height: 781px; overflow: hidden; }
  body {
    background: var(--backdrop);
    font-family: "Open Sans", sans-serif;
    position: relative;
  }
  .card {
    position: absolute;
    top: 247px;
    width: 500px;
    height: 286px;
    border-radius: 20px;
  }
  .card-front { left: 70px; background: var(--card-white); color: var(--ink); }
  .card-back  { left: 630px; background: var(--card-black); }

  .holder { position: absolute; left: 32px; top: 26px; }
  .holder-name { font-weight: 700; font-size: 16px; letter-spacing: 0.06em; text-transform: uppercase; line-height: 1.3; }
  .holder-title { font-size: 11.5px; color: var(--ink-soft); margin-top: 1px; }

  .address { position: absolute; left: 32px; top: 92px; font-size: 12px; line-height: 1.4; color: var(--ink-soft); }

  .contacts { position: absolute; left: 32px; top: 148px; list-style: none; font-size: 12.5px; line-height: 1.45; color: var(--ink); }
  .contacts li { display: flex; align-items: center; gap: 7px; }
  .contacts svg { width: 11px; height: 11px; fill: var(--ink); flex: none; }

  .wordmark {
    position: absolute;
    font-weight: 800;
    text-transform: uppercase;
    letter-spacing: 0.01em;
    line-height: 1;
  }
  .card-front .wordmark { right: 30px; bottom: 30px; font-size: 25px; color: var(--ink); text-align: right; line-height: 1.05; }
  .card-back .wordmark { left: 0; right: 0; top: 124px; text-align: center; font-size: 34px; color: var(--gloss); }
</style>
</head>
<body>
  <section class="card card-front">
    <div class="holder">
      <p class="holder-name">Maren Okafor</p>
      <p class="holder-title">Director</p>
    </div>
    <p class="address">48 Linden Row, Suite 210<br>Orlando, FL 32899</p>
    <ul class="contacts">
      <li><svg viewBox="0 0 12 12" aria-hidden="true"><path d="M2.5 0.5l2 2.6-1.1 1.3c.7 1.6 1.9 2.8 3.3 3.4l1.3-1.1 2.5 2-1.2 2.2C5 10.6 1.4 7 .3 1.8z"/></svg>(555) 310-4827</li>
      <li><svg viewBox="0 0 12 12" aria-hidden="true"><path d="M3 0h6v12H3zM4 1.5v7.5h4V1.5z"/></svg>(555) 310-4830</li>
      <li><svg viewBox="0 0 12 12" aria-hidden="true"><path d="M0 2h12v8H0zM1.2 3.2v.4L6 6.8l4.8-3.2v-.4z"/></svg>hello@brookvanedrafting.com</li>
      <li><svg viewBox="0 0 12 12" aria-hidden="true"><path d="M6 0a6 6 0 100 12A6 6 0 006 0zm0 1.2c.9 0 1.7 2 1.8 4.2H4.2C4.3 3.2 5.1 1.2 6 1.2zM4.2 6.6h3.6C7.7 8.8 6.9 10.8 6 10.8S4.3 8.8 4.2 6.6z"/></svg>www.brookvanedrafting.com</li>
    </ul>
    <p class="wordmark">Brookvane<br>Drafting</p>
  </section>

  <section class="card card-back">
    <p class="wordmark">Brookvane Drafting</p>
  </section>
</body>
</html>
```